Fenwick Grading LTD - website for irrigation & Landscape Lighting & Buried service wire

Looking for a website to help promote my business with Irrigation (installation, service, etc) and buried service wire/drainage solutions.

Commercial/Residential

Landscape lighting.

I’ll get photos in the trucks and trailers to upload as well maybe the machine as well.

Target Market(s)

Homeowners who want green grass and beautiful gardens. Beautiful landscape lighting

Industry/Entity Type

Irrigation systems and landscape lighting and buried service wire to homes and offering Drainage soltions.

Coding

Coded - Design and coding required

Number of Pages Required

4 page

Colors
F0912C
F2A743
F7CA91
FBE8D2
FDF5EE

Requirements
Must have
• was hoping to link up my email on fenwickgrading@mailbox-example.net with the website if possible.
Nice to have
• Page for Irrigation, page for landscape lighting, page buried service wire & drainage soltions.

```html
<!DOCTYPE html>
<html lang="en">
<head>
<meta charset="utf-8">
<title>Fenwick Grading LTD</title>
<link href="https://fonts.googleapis.com/css2?family=Montserrat:wght@400;500;600;700;800&family=Playfair+Display:wght@800;900&display=swap" rel="stylesheet">
<style>
:root{
  --orange:#F0912C;
  --orange-2:#F2A743;
  --peach:#F7CA91;
  --sand:#FBE8D2;
  --cream:#FDF5EE;
  --ink:#1c1c1c;
  --text:#333;
  --white:#fff;
}
*{margin:0;padding:0;box-sizing:border-box}
html,body{width:1200px;height:4354px;overflow:hidden}
body{position:relative;background:var(--white);font-family:'Montserrat',sans-serif;color:var(--text)}

/* header */
.site-header{position:absolute;left:0;top:0;width:1200px;height:70px;z-index:5}
.brand{position:absolute;left:140px;top:18px;display:flex;align-items:center;gap:8px;font-weight:700;color:var(--orange);font-size:15px;letter-spacing:.5px;line-height:1.15}
.brand-dot{width:14px;height:14px;border-radius:50%;background:var(--orange)}
.main-nav a{position:absolute;top:27px;font-size:13px;font-weight:500;color:var(--ink);text-decoration:none;white-space:nowrap}
.main-nav a.active{color:var(--orange);border-bottom:2px solid var(--orange);padding-bottom:3px}
.btn-contact{position:absolute;left:940px;top:18px;width:118px;height:35px;border-radius:18px;background:var(--white);color:var(--orange);font-size:11px;font-weight:600;display:flex;align-items:center;justify-content:center;box-shadow:0 2px 8px rgba(0,0,0,.12)}

/* hero */
.hero{position:absolute;left:0;top:0;width:1200px;height:557px;background:var(--cream);overflow:hidden}
.hero-photo{position:absolute;left:0;top:0}
.hero-title{position:absolute;left:140px;top:205px;font-size:31px;font-weight:500;color:var(--ink);line-height:47px}
.hero-title .hl{color:var(--orange);font-weight:600}
.hero-sub{position:absolute;left:140px;top:363px;width:420px;padding-left:12px;border-left:2px solid var(--orange);font-size:12.5px;line-height:22px;color:var(--ink);font-weight:500}
.btn{position:absolute;border-radius:26px;background:var(--orange);color:var(--ink);font-weight:600;font-size:12px;display:flex;align-items:center;justify-content:center;text-transform:uppercase}
.btn-quote{left:140px;top:432px;width:162px;height:33px;color:var(--white);font-size:11.5px}

/* sections */
.section-title{position:absolute;left:0;width:1200px;text-align:center;font-family:'Playfair Display',serif;font-weight:900;font-size:31px;color:var(--ink);letter-spacing:.3px}
.photo-frame{position:absolute;border:1.5px solid var(--orange);border-radius:24px;border-right:none;border-bottom:none}
.photo{position:absolute;border-radius:20px}
.svc-kicker{position:absolute;font-size:24px;font-weight:800;color:var(--orange);text-transform:uppercase;white-space:nowrap}
.svc-sub{position:absolute;font-size:21px;font-weight:600;color:var(--ink);line-height:35px}
.svc-text{position:absolute;font-size:15.5px;line-height:25.5px;color:var(--text)}
.btn-more{width:146px;height:51px;font-size:12px}

.lighting-band{position:absolute;left:0;top:1360px}
.reviews-band{position:absolute;left:0;top:3110px;width:1200px;height:800px;background:linear-gradient(var(--white),var(--cream) 30%,var(--cream) 70%,var(--white))}

/* testimonials */
.avatar{position:absolute;width:112px;height:112px;border-radius:50%;background:var(--white);box-shadow:0 4px 14px rgba(0,0,0,.14);display:flex;align-items:center;justify-content:center}
.avatar span{width:86px;height:86px;border-radius:50%;background:linear-gradient(#8b8f98,#3a3d44)}
.quote{position:absolute;width:280px;text-align:center;font-size:13px;line-height:21px;color:var(--ink);font-weight:500}
.quote-name{position:absolute;width:280px;text-align:center;font-size:13px;font-weight:600;color:var(--orange);text-transform:uppercase}
.quote-role{position:absolute;width:280px;text-align:center;font-size:11px;color:var(--ink);font-weight:500}
.divider{position:absolute;top:3410px;width:1px;height:180px;background:#ccc}
.dot{position:absolute;width:14px;height:14px;border-radius:50%;background:var(--sand)}
.dot.on{width:22px;height:22px;border:4px solid var(--orange);background:var(--white)}

/* footer */
.footer-brand{position:absolute;left:140px;top:4040px;font-size:34px;font-weight:700;color:var(--orange);line-height:1.05}
.footer-brand small{font-size:34px}
.footer-about{position:absolute;left:140px;top:4147px;width:340px;font-size:13px;line-height:21px;color:var(--ink)}
.social{position:absolute;top:4234px;width:33px;height:33px;border-radius:50%;border:1.5px solid var(--orange)}
.social.fill{background:var(--orange)}
.foot-head{position:absolute;top:4025px;font-size:25px;font-weight:600;color:var(--orange)}
.foot-links a{position:absolute;left:595px;font-size:12.5px;color:var(--ink);text-decoration:none;white-space:nowrap}
.contact-item{position:absolute;left:835px;display:flex;gap:12px;font-size:12.5px;line-height:20px;color:var(--ink)}
.contact-item svg{flex:none;margin-top:2px}
.bottom-bar{position:absolute;left:0;top:4318px;width:1200px;height:36px;background:var(--orange);font-size:12px;color:var(--ink);font-weight:500}
.bottom-bar .copy{position:absolute;left:140px;top:10px}
.bottom-bar .legal{position:absolute;left:792px;top:12px;font-size:11px}
</style>
</head>
<body>

<section class="hero">
  <svg class="hero-photo" width="1200" height="557" role="img" aria-label="Photo of a garden sprinkler spraying water across a sunlit lawn with trees">
    <defs>
      <linearGradient id="lawn" x1="0" y1="0" x2="0" y2="1">
        <stop offset="0" stop-color="#9fb3c4"/>
        <stop offset=".35" stop-color="#e8c47a"/>
        <stop offset=".6" stop-color="#9a9a3a"/>
        <stop offset="1" stop-color="#3f5a1e"/>
      </linearGradient>
    </defs>
    <path d="M850 0 C800 60 760 120 700 170 C640 220 630 300 650 360 C680 420 760 390 860 410 C960 430 960 520 1040 552 L1200 557 L1200 0 Z" fill="url(#lawn)" stroke="var(--orange)" stroke-width="5"/>
  </svg>
  <h1 class="hero-title">Welcome To <span class="hl">Fenwick Grading</span><br>Your One-Stop Solution For<br>Home Improvement</h1>
  <p class="hero-sub">Expertise In Irrigation, Landscape Lighting, Service Wire And Drainage Solutions</p>
  <div class="btn btn-quote">Get A Free Quote</div>
</section>

<header class="site-header">
  <div class="brand"><span class="brand-dot"></span><span>FENWICK<br>GRADING LTD</span></div>
  <nav class="main-nav">
    <a class="active" style="left:386px">Home</a>
    <a style="left:452px">Irrigation</a>
    <a style="left:539px">Landscape Lighting</a>
    <a style="left:694px">Service Wire &amp; Drainage</a>
  </nav>
  <div class="btn-contact">CONTACT US</div>
</header>

<!-- Irrigation -->
<h2 class="section-title" style="top:650px">IRRIGATION SYSTEMS</h2>
<div class="photo-frame" style="left:157px;top:750px;width:395px;height:500px"></div>
<div class="photo" role="img" aria-label="Photo of an irrigation sprinkler head spraying over green grass" style="left:170px;top:763px;width:433px;height:499px;background:linear-gradient(160deg,#c9d2c0,#6f9a4a 45%,#3e6b24)"></div>
<div class="svc-kicker" style="left:670px;top:840px">Efficient and Effective</div>
<div class="svc-sub" style="left:670px;top:875px">Watering Solutions for Your<br>Lawn and Garden</div>
<p class="svc-text" style="left:670px;top:955px;width:385px">Our irrigation systems are designed to provide your lawn and garden with the right amount of water, without wasting a single drop. With our expert installation and service, you can rest assured that your plants will receive the nourishment they need to thrive.</p>
<div class="btn btn-more" style="left:670px;top:1126px">Learn More</div>

<!-- Landscape lighting -->
<svg class="lighting-band" width="1200" height="920" aria-hidden="true">
  <path d="M0 62 C150 100 300 60 500 40 C700 20 800 90 950 60 C1060 40 1140 20 1200 40 L1200 920 C1100 900 1000 870 850 890 C700 910 650 870 500 860 C300 850 150 920 0 890 Z" fill="var(--cream)"/>
</svg>
<h2 class="section-title" style="top:1540px">LANDSCAPE LIGHTING</h2>
<div class="svc-kicker" style="left:140px;top:1718px">Enhance Your Outdoor</div>
<div class="svc-sub" style="left:140px;top:1753px">Space with Beautiful and Functional<br>Lighting Solutions</div>
<p class="svc-text" style="left:140px;top:1834px;width:395px">Our landscape lighting solutions are designed to enhance the beauty and functionality of your outdoor space. From subtle pathway lighting to dramatic spotlights, we'll work with you to create a lighting plan that meets your needs and complements your landscape.</p>
<div class="btn btn-more" style="left:140px;top:2007px">Learn More</div>
<div class="photo" role="img" aria-label="Photo of a lush garden with a lawn and wooden fence" style="left:607px;top:1641px;width:452px;height:504px;background:linear-gradient(170deg,#dfe8d0,#4f8a2e 40%,#77a848 70%,#8a6a3a)"></div>

<!-- Buried service wire & drainage -->
<h2 class="section-title" style="top:2405px">SERVICE WIRE &amp; DRAINAGE</h2>
<div class="photo-frame" style="left:157px;top:2505px;width:395px;height:500px"></div>
<div class="photo" role="img" aria-label="Photo of a trench dug across a yard for buried service wire and drainage pipe" style="left:170px;top:2518px;width:433px;height:499px;background:linear-gradient(135deg,#5a3a28,#8a5a3c 45%,#b08a64 70%,#4f6b2e)"></div>
<div class="svc-kicker" style="left:670px;top:2596px">Expert Installation of</div>
<div class="svc-sub" style="left:670px;top:2630px">Buried Service Wire and<br>Drainage Solutions</div>
<p class="svc-text" style="left:670px;top:2710px;width:390px">Our team of experienced professionals will trench and bury your service wire with precision and care. We also design drainage solutions that move water away from your home, protecting your foundation, lawn and garden for years to come.</p>
<div class="btn btn-more" style="left:670px;top:2883px">Learn More</div>

<!-- Testimonials -->
<div class="reviews-band"></div>
<h2 class="section-title" style="top:3265px">WHAT OUR CUSTOMERS SAY</h2>

<div class="avatar" style="left:231px;top:3391px" role="img" aria-label="Customer portrait"><span></span></div>
<div class="avatar" style="left:544px;top:3391px" role="img" aria-label="Customer portrait"><span style="background:linear-gradient(#c9a58f,#8a1f2a)"></span></div>
<div class="avatar" style="left:857px;top:3391px" role="img" aria-label="Customer portrait"><span style="background:linear-gradient(#5a4a40,#1e1e22)"></span></div>
<div class="divider" style="left:445px"></div>
<div class="divider" style="left:757px"></div>

<p class="quote" style="left:147px;top:3535px">Lorem ipsum dolor sit amet, consectetur adipiscing elit, sed do eiusmod tempor commodo viverra maecenas vel facilisis.</p>
<div class="quote-name" style="left:147px;top:3618px">Owen Marsh</div>
<div class="quote-role" style="left:147px;top:3639px">Grodon Tower</div>

<p class="quote" style="left:460px;top:3535px">Lorem ipsum dolor sit amet, consectetur adipiscing elit, sed do eiusmod tempor commodo viverra maecenas vel facilisis.</p>
<div class="quote-name" style="left:460px;top:3618px">Clara Dunn</div>
<div class="quote-role" style="left:460px;top:3639px">Grodon Tower</div>

<p class="quote" style="left:773px;top:3535px">Lorem ipsum dolor sit amet, consectetur adipiscing elit, sed do eiusmod tempor commodo viverra maecenas vel facilisis.</p>
<div class="quote-name" style="left:773px;top:3618px">Felix Rowe</div>
<div class="quote-role" style="left:773px;top:3639px">Grodon Tower</div>

<span class="dot" style="left:529px;top:3723px"></span>
<span class="dot on" style="left:559px;top:3719px"></span>
<span class="dot" style="left:597px;top:3723px"></span>
<span class="dot" style="left:627px;top:3723px"></span>
<span class="dot" style="left:656px;top:3723px"></span>

<!-- Footer -->
<footer>
  <div class="footer-brand">FENWICK<br>GRADING LTD</div>
  <p class="footer-about">Lorem ipsum dolor sit amet, consectetur adipiscing elit, sed do eiusmod tempor incididunt ut labore et dolore magna aliqua. Quis ipsum.</p>
  <span class="social" style="left:144px" aria-label="Social link"></span>
  <span class="social fill" style="left:190px" aria-label="Social link"></span>
  <span class="social" style="left:238px" aria-label="Social link"></span>
  <span class="social" style="left:284px" aria-label="Social link"></span>

  <h3 class="foot-head" style="left:585px">Quick Links</h3>
  <nav class="foot-links">
    <a style="top:4075px">Home</a>
    <a style="top:4110px">Irrigation</a>
    <a style="top:4145px">Landscape Lighting</a>
    <a style="top:4180px">Service Wire &amp; Drainage</a>
    <a style="top:4215px">Contact</a>
  </nav>

  <h3 class="foot-head" style="left:832px">Contact Info</h3>
  <div class="contact-item" style="top:4072px">
    <svg width="18" height="20" viewBox="0 0 18 20"><path d="M9 1a6.5 6.5 0 0 0-6.5 6.5C2.5 12 9 19 9 19s6.5-7 6.5-11.5A6.5 6.5 0 0 0 9 1z" fill="none" stroke="#333" stroke-width="1.4"/><circle cx="9" cy="7.5" r="2.3" fill="none" stroke="#333" stroke-width="1.4"/></svg>
    <span>Address 1, Address 2, Address 3,<br>Address 4.</span>
  </div>
  <div class="contact-item" style="top:4138px">
    <svg width="18" height="18" viewBox="0 0 18 18"><path d="M4 1.5l3 3-1.8 2a10 10 0 0 0 5.3 5.3l2-1.8 3 3-2 2.5C7.5 15 3 10.5 1.5 3.5z" fill="none" stroke="#333" stroke-width="1.3" stroke-linejoin="round"/></svg>
    <span>0123456789</span>
  </div>
  <div class="contact-item" style="top:4186px">
    <svg width="18" height="16" viewBox="0 0 18 16"><rect x="1" y="2" width="16" height="12" rx="1" fill="none" stroke="#333" stroke-width="1.3"/><path d="M1 3l8 6 8-6" fill="none" stroke="#333" stroke-width="1.3"/></svg>
    <span>fenwickgrading@mailbox-example.net</span>
  </div>

  <div class="bottom-bar">
    <span class="copy">©2024 FenwickGrading. All Rights reserved.</span>
    <span class="legal">PRIVACY TERMS &nbsp;&nbsp;&nbsp; | &nbsp;&nbsp;&nbsp; TERMS &amp; CONDITIONS</span>
  </div>
</footer>

</body>
</html>
```